Kelvor Engineers: Why you should hire us keepsake

New design. Open to plastic cards. We are an engineering firm that designs cell phone towers and commercial buildings. Please check out our website www.kelvorstruct.com for more details. We want people to remember our card and for it to be useful if possible. We want the same look and feel on these cards to be translated to other marketing material we may need such as brochures.

Target Market(s)

Architects, Developers and Telecommunication Carriers

Industry/Entity Type

Engineering

Contact Information for Business Card

Card with our company colors, logo, and innovative design with elements related to our industry.

Font styles to use
Sans Serif

Colors
9bcb3c
abd036
0255a3

Requirements
Must have
• Sleek and hip design
Nice to have
• Bright lime green and navy coloring that pops with an innovative design.
Should not have
• A basic and boring design

```html
<!DOCTYPE html>
<html lang="en">
<head>
<meta charset="utf-8">
<title>Kelvor Engineers – Business Card</title>
<link rel="stylesheet" href="https://fonts.googleapis.com/css2?family=Montserrat:wght@500;600;800;900&family=Oswald:wght@600&display=swap">
<style>
  :root {
    --navy: #1c3566;
    --navy-deep: #162c57;
    --lime: #cfd62a;
    --white: #ffffff;
    --stage: #2b2b2d;
  }
  * { margin: 0; padding: 0; box-sizing: border-box; }
  html, body { width: 1200px; height: 930px; overflow: hidden; }
  body { background: var(--stage); font-family: "Montserrat", sans-serif; position: relative; }

  .card {
    position: absolute;
    width: 520px;
    height: 300px;
    border-radius: 22px;
    overflow: hidden;
  }

  /* Back of card */
  .card-back { left: 90px; top: 110px; background: var(--navy); }
  .card-back .wordmark {
    position: absolute; left: 0; right: 0; top: 86px;
    text-align: center;
    font-weight: 900; font-size: 84px; letter-spacing: 2px;
    color: var(--lime);
  }
  .card-back .cities {
    position: absolute; left: 0; right: 0; bottom: 40px;
    text-align: center;
    font-weight: 600; font-size: 15px; letter-spacing: 1.5px;
    color: var(--white);
  }
  .cities .sep { color: var(--lime); margin: 0 6px; }

  /* Front of card */
  .card-front { left: 590px; top: 520px; background: var(--white); }
  .card-front .swoosh { position: absolute; inset: 0; width: 100%; height: 100%; }
  .card-front .wordmark {
    position: absolute; left: 0; right: 0; top: 30px;
    text-align: center;
    font-weight: 900; font-size: 64px; letter-spacing: 2px;
    color: var(--navy);
  }
  .card-front .tagline {
    position: absolute; left: 0; right: 0; top: 112px;
    text-align: center;
    font-weight: 800; font-size: 13px; letter-spacing: 1.4px;
    color: var(--navy);
  }
  .person {
    position: absolute; left: 56px; top: 226px; width: 200px;
    text-align: right;
  }
  .person .name {
    font-family: "Oswald", sans-serif; font-weight: 600;
    font-size: 24px; letter-spacing: 0.5px; line-height: 1;
    color: var(--white); text-transform: uppercase;
  }
  .person .role { font-size: 13px; font-weight: 500; color: var(--lime); margin-top: 4px; }
  .divider {
    position: absolute; left: 276px; top: 216px;
    width: 1px; height: 68px; background: rgba(255,255,255,0.6);
  }
  .contact-list {
    position: absolute; left: 292px; top: 212px;
    list-style: none;
  }
  .contact-list li {
    display: flex; align-items: center; gap: 8px;
    font-size: 12px; font-weight: 500; line-height: 18px;
    color: var(--white);
  }
  .contact-list svg { width: 10px; height: 10px; flex: none; }
</style>
</head>
<body>

<section class="card card-back" aria-label="Card back">
  <div class="wordmark">KELVOR</div>
  <p class="cities">ATLANTA<span class="sep">|</span>CHARLOTTE<span class="sep">|</span>HOUSTON<span class="sep">|</span>SAN ANTONIO</p>
</section>

<section class="card card-front" aria-label="Card front">
  <svg class="swoosh" viewBox="0 0 520 300" preserveAspectRatio="none" aria-hidden="true">
    <path d="M0 176 Q300 218 520 94 L520 300 L0 300 Z" fill="var(--navy-deep)"/>
    <path d="M0 182 Q300 226 520 104 L520 140 Q300 236 0 206 Z" fill="var(--lime)"/>
    <path d="M0 206 Q300 236 520 140 L520 300 L0 300 Z" fill="var(--navy)"/>
  </svg>
  <div class="wordmark">KELVOR</div>
  <p class="tagline">MULTI-DISCIPLINE ENGINEERING</p>

  <div class="person">
    <p class="name">Dana Whitlock</p>
    <p class="role">Director</p>
  </div>
  <div class="divider"></div>
  <ul class="contact-list">
    <li><svg viewBox="0 0 10 10"><path d="M2 1 L4 1 L4.6 3 L3.4 3.8 Q4.4 5.8 6.2 6.6 L7 5.4 L9 6 L9 8 Q8.6 9 7.6 9 Q1 8.4 1 2.4 Q1 1.4 2 1 Z" fill="var(--lime)"/></svg>555.014.2325</li>
    <li><svg viewBox="0 0 10 10"><rect x="2.5" y="0.5" width="5" height="9" rx="1" fill="none" stroke="var(--lime)" stroke-width="1.2"/></svg>555.019.5887</li>
    <li><svg viewBox="0 0 10 10"><rect x="0.6" y="2" width="8.8" height="6" fill="none" stroke="var(--lime)" stroke-width="1.1"/><path d="M0.6 2 L5 5.6 L9.4 2" fill="none" stroke="var(--lime)" stroke-width="1.1"/></svg>dwhitlock@kelvorstruct.com</li>
    <li><svg viewBox="0 0 10 10"><circle cx="5" cy="5" r="4.4" fill="var(--lime)"/></svg>www.kelvorstruct.com</li>
  </ul>
</section>

</body>
</html>
```